Financial Advisor Resource Firm needs business card design

Need business card design for company in Omaha NE called Meridale Circle. We provide resources to financial advisors....workshop programs, retirement analysis, and insurance planning. I would like to see designs that use grays, greens, black, and white colors. The final design should communicate 'collaboration' and be simple yet attractive to financial planning clients. I will attached our logo and another picture of a puzzle piece coming together. I would like the incorporate the puzzle picture somehow, maybe on the back somehow, with color or just the gray scale....OR, the picture be the front of the card with 'Meridale' definition on it (see upload) and then company logo, employee name, title, address on the back (see ppt uploaded). The following disclosure needs to be included somewhere- Advisory services offered through Stonebrook Assets, LLC.
Updates

I uploaded a svg and ai file of the logo

Target Market(s)

Financial planning clients and financial advisors....so pretty diverse age range of about 40-70.

Industry/Entity Type

Financial Planning

Contact Information for Business Card

Tobias L. Fenwright, MBA
Founder/President
5287 E. Larkin Road
Suite 230
Omaha, NE 68190
Phone- (402) 555-0147
Cell- (402) 555-0183
Fax- (402) 555-0129
email- tobias@meridaleplan.example
web address- www.meridaleplan.example

Colors
1b1b1b
474747
d3d3d3
ffffff
9bcb3c
abd036

Requirements
Must have
• Must include logo provided, must be 2 sided, and must have disclosure...all of these items listed in project description

```html
<!DOCTYPE html>
<html lang="en">
<head>
<meta charset="utf-8">
<title>Meridale Circle — Business Card</title>
<link rel="stylesheet" href="https://fonts.googleapis.com/css2?family=Jost:wght@400;500&family=Arimo:wght@400&display=swap">
<style>
  :root {
    --ink: #1b1b1b;
    --charcoal: #474747;
    --mist: #d3d3d3;
    --paper: #ffffff;
    --leaf: #9bcb3c;
    --lime: #abd036;
    --stage: #0d0d0d;
  }
  * { box-sizing: border-box; margin: 0; padding: 0; }
  html, body { width: 1200px; height: 1200px; overflow: hidden; }
  body {
    background: var(--stage);
    display: flex;
    align-items: center;
    justify-content: center;
    font-family: "Jost", sans-serif;
  }
  .card-spread { display: flex; }
  .card { width: 580px; height: 338px; position: relative; overflow: hidden; }

  /* back side */
  .card-back {
    background: radial-gradient(ellipse at 55% 60%, #3a3a3a 0%, #262626 45%, #141414 100%);
  }
  .card-back .photo-fill {
    position: absolute; inset: 0;
    background: linear-gradient(160deg, rgba(90,90,90,.35) 0%, rgba(30,30,30,.2) 40%, rgba(0,0,0,.55) 100%);
  }
  .back-wordmark {
    position: absolute; left: 0; right: 0; top: 148px;
    text-align: center;
    color: var(--paper);
    font-size: 36px; font-weight: 400;
    letter-spacing: 1px;
  }
  .back-url {
    position: absolute; left: 0; right: 0; top: 250px;
    text-align: center;
    color: var(--leaf);
    font-size: 13px; letter-spacing: 3.5px;
  }
  .disclosure {
    position: absolute; left: 0; right: 0; bottom: 14px;
    text-align: center;
    color: var(--mist);
    font-family: "Arimo", sans-serif; font-size: 10px; letter-spacing: .3px;
  }

  /* front side */
  .card-front { background: var(--paper); color: var(--ink); }
  .front-mark { position: absolute; left: 18px; top: 40px; }
  .front-wordmark {
    position: absolute; right: 30px; top: 40px;
    font-size: 28px; font-weight: 400; color: var(--ink);
    letter-spacing: .5px;
  }
  .holder-name {
    position: absolute; right: 30px; top: 120px;
    font-size: 22px; color: var(--leaf);
  }
  .holder-title {
    position: absolute; right: 30px; top: 150px;
    font-size: 18px; color: var(--ink);
  }
  .address {
    position: absolute; right: 38px; top: 200px;
    font-family: "Arimo", sans-serif; font-size: 14px; line-height: 18px;
    text-align: right;
  }
  .rule {
    position: absolute; left: 550px; top: 202px; width: 3px; bottom: 0;
    background: var(--ink);
  }
  .contact-bar {
    position: absolute; left: 110px; right: 0; top: 264px; height: 22px;
    background: var(--leaf);
    display: flex; align-items: center; gap: 18px;
    padding-left: 16px;
    font-family: "Arimo", sans-serif; font-size: 14px; color: var(--paper);
  }
  .contact-item { display: flex; align-items: center; gap: 4px; white-space: nowrap; }
  .contact-item svg { width: 12px; height: 12px; fill: var(--ink); }
  .email-line {
    position: absolute; right: 38px; top: 292px;
    display: flex; align-items: center; gap: 5px;
    font-family: "Arimo", sans-serif; font-size: 14px;
  }
  .email-line svg { width: 12px; height: 9px; fill: var(--leaf); }
</style>
</head>
<body>
  <main class="card-spread">
    <section class="card card-back" aria-label="Card back">
      <div class="photo-fill" role="img" aria-label="Grayscale photo of hands joining puzzle pieces together"></div>
      <div class="back-wordmark">Meridale Circle</div>
      <div class="back-url">www.meridaleplan.example</div>
      <p class="disclosure">Advisory services offered through Stonebrook Assets, LLC</p>
    </section>

    <section class="card card-front" aria-label="Card front">
      <svg class="front-mark" width="210" height="210" viewBox="0 0 210 210" aria-hidden="true">
        <circle cx="105" cy="105" r="100" fill="var(--mist)"/>
      </svg>
      <div class="front-wordmark">Meridale Circle</div>
      <div class="holder-name">Tobias L. Fenwright, MBA</div>
      <div class="holder-title">Founder/President</div>
      <div class="address">5287 E. Larkin Road,<br>Suite 230<br>Omaha, NE 68190</div>
      <div class="rule"></div>
      <div class="contact-bar">
        <span class="contact-item">
          <svg viewBox="0 0 24 24"><path d="M6.6 10.8a15.1 15.1 0 0 0 6.6 6.6l2.2-2.2c.3-.3.7-.4 1-.2 1.1.4 2.3.6 3.6.6.6 0 1 .4 1 1V20c0 .6-.4 1-1 1A17 17 0 0 1 3 4c0-.6.4-1 1-1h3.5c.6 0 1 .4 1 1 0 1.3.2 2.5.6 3.6.1.3 0 .7-.2 1z"/></svg>
          : (402) 555-0147
        </span>
        <span class="contact-item">
          <svg viewBox="0 0 24 24"><path d="M7 1h10a2 2 0 0 1 2 2v18a2 2 0 0 1-2 2H7a2 2 0 0 1-2-2V3a2 2 0 0 1 2-2zm0 3v14h10V4zm5 15.5a1 1 0 1 0 0 2 1 1 0 0 0 0-2z"/></svg>
          : (402) 555-0183
        </span>
        <span class="contact-item">
          <svg viewBox="0 0 24 24"><path d="M6 2h10l2 2v5H6zm-2 8h16a2 2 0 0 1 2 2v6h-4v4H6v-4H2v-6a2 2 0 0 1 2-2zm4 7v3h8v-3z"/></svg>
          : (402) 555-0129
        </span>
      </div>
      <div class="email-line">
        <svg viewBox="0 0 24 18"><path d="M0 0h24v18H0zm2 2v1l10 7 10-7V2z"/></svg>
        : tobias@meridaleplan.example
      </div>
    </section>
  </main>
</body>
</html>
```